A Greens Sunrise Website Design

I have hosting set up through Net Harbor but need Web Design for a new company called A Greens Sunrise. I am a holistic health coach helping individuals and groups achieve optimum health through the elimination of processed foods, GMOs, animal foods and chemical toxins in foods, beauty and household products and the promotion of a plant focused diet. I provide education and coaching programs to ensure success. The site should include my logo, the colors of black, white, orange and green and convey a simple, natural and friendly tone. My goal is to be a friendly resource to those who want or need to transition to a vegan lifestyle but don't want to feel judged or the need to be perfect to heal and make a difference. Progress vs perfection.
Updates

The tabs would be: Home About Services Recipes Resources (Things I Love) I.e affiliate links Contact Possibly a calendar of events As for products, they would be simple ebooks or 30 day programs delivered electronically. They are still in development. I will have a link to a free book excerpt for opting into my mailing list. You can see a site I built through my school's hosting for a basic example at Lorindakpelham.example While I like the basic bones of it, I wanted something more robust and not tied to the school.

```html
<!DOCTYPE html>
<html lang="en">
<head>
<meta charset="utf-8">
<title>A Greens Sunrise</title>
<link rel="stylesheet" href="https://fonts.googleapis.com/css2?family=Ubuntu:wght@300;400&family=Open+Sans:wght@400;600&family=Exo:wght@400;600&family=Courgette&display=swap">
<style>
:root{
  --green:#6cbf3c;
  --green-dark:#4f9e28;
  --orange:#f7941d;
  --orange-light:#fbb040;
  --panel:#f2f3f4;
  --border:#d6d8da;
  --text:#444;
  --dark:#222;
}
*{margin:0;padding:0;box-sizing:border-box}
html,body{width:873px;height:1200px;overflow:hidden;background:#fff}
body{position:relative;font-family:"Open Sans",sans-serif;color:var(--text)}
.abs{position:absolute}
.top-bar{left:0;top:0;width:873px;height:6px;background:var(--green)}
.brand-name{left:72px;top:44px;font-family:"Ubuntu",sans-serif;font-weight:400;font-size:15px;color:var(--dark)}
.contact{right:73px;top:37px;text-align:right;font-size:10.5px;line-height:18px;color:var(--dark)}
.contact span{color:var(--green)}
.band{left:0;top:160px;width:873px;height:211px;background:linear-gradient(#8ccf55,#5fae2f);border-top:4px solid var(--orange);border-bottom:4px solid var(--orange)}
.panel{left:72px;top:94px;width:729px;height:1018px;background:var(--panel);border:1px solid var(--border);border-radius:3px}
.nav{left:72px;top:94px;width:729px;height:39px;background:linear-gradient(#fbae3c,var(--orange));display:flex;border-radius:3px 3px 0 0}
.nav a{color:#fff;text-decoration:none;font-size:11px;display:flex;align-items:center;justify-content:center;border-right:1px solid #e0811a}
.nav a:last-child{border-right:none}
.hero{left:73px;top:133px;width:727px;height:261px;background:linear-gradient(120deg,#c9a27c,#e7d3b8 45%,#b98b62 80%,#d9c2a4)}
.hero-caption{left:128px;top:219px;width:296px;height:59px;background:rgba(60,60,60,.72);color:#fff;font-family:"Exo",sans-serif;font-size:28px;display:flex;align-items:center;justify-content:center;white-space:nowrap}
.hero-caption b{font-weight:600;font-size:22px;margin:0 6px}
.dots{left:400px;top:377px;display:flex;gap:5px}
.dot{width:10px;height:10px;border-radius:50%;border:1.5px solid #555;background:#fff}
.dot.on{background:var(--green);border-color:var(--green)}
h2{font-family:"Ubuntu",sans-serif;font-weight:300;color:var(--green);font-size:24px;white-space:nowrap}
.welcome-text{left:94px;top:450px;width:448px;font-size:8.6px;line-height:16px}
.more{font-size:9px;color:var(--dark);white-space:nowrap}
.video{left:554px;top:414px;width:224px;height:148px;border-radius:12px;border:1px solid #ccc;background:radial-gradient(circle at 50% 55%,#e2b463,#c8d39a 40%,#e6e8ea 75%)}
.card{top:645px;width:212px;height:139px;border:1px solid #ccc}
.card-title{font-family:"Ubuntu",sans-serif;font-size:13px;color:var(--orange)}
.small{font-size:8.8px;line-height:16.5px}
.spec{font-size:8.8px;line-height:22px}
.spec td{vertical-align:top}
.spec td:first-child{color:var(--orange);width:53px}
.food-tips{font-family:"Courgette",cursive;color:#fff;font-size:23px}
.btn{color:#fff;font-size:10px;display:flex;align-items:center;justify-content:center;border-radius:2px;white-space:nowrap}
.newsletter{left:564px;top:799px;width:212px;height:117px;background:linear-gradient(135deg,var(--orange-light),var(--orange));color:#fff;padding:8px 10px}
.newsletter h3{font-family:"Ubuntu",sans-serif;font-weight:400;font-size:13px}
.newsletter p{font-size:8px;line-height:13px;margin-top:4px}
.field{width:188px;height:22px;background:#fff;border:1px solid #ddd;margin-top:6px;font-size:8px;color:#777;padding:5px 7px}
.rule{left:183px;top:978px;width:320px;height:1px;background:#ccc}
.avatar{width:66px;height:66px;border-radius:50%;border:4px solid #bbb;background:linear-gradient(#c9b3a2,#7b6b60)}
.quote-title{font-size:9px;color:var(--orange);white-space:nowrap}
.quote{font-size:9.5px;line-height:13px;color:var(--dark);width:140px}
.footer-links{left:71px;top:1130px;font-size:13px;color:var(--dark);font-family:"Ubuntu",sans-serif;font-weight:300;white-space:nowrap}
.footer-links i{font-style:normal;margin:0 6px}
.copy{left:72px;top:1156px;font-size:9px;color:#555}
.social{left:712px;top:1133px;display:flex;gap:6px}
.social span{width:17px;height:17px;border-radius:2px;background:#8a9aa8}
</style>
</head>
<body>
<div class="abs top-bar"></div>
<div class="abs brand-name">A Greens Sunrise</div>
<div class="abs contact"><div><span>Phone:</span> +42 555-01-27</div><div><span>E-Mail:</span> hello@greenssunrise.example</div></div>

<div class="abs band"></div>
<div class="abs panel"></div>
<nav class="abs nav">
  <a style="width:73px">Home</a><a style="width:81px">About Us</a><a style="width:88px">Services</a><a style="width:88px">Health Tips</a><a style="width:108px">Testimonials</a><a style="width:75px">Exercise</a><a style="width:116px">Body Fittness</a><a style="width:100px">Contact Us</a>
</nav>

<div class="abs hero" role="img" aria-label="Family sharing a meal around a dinner table"></div>
<div class="abs hero-caption">Progress<b>VS</b>Perfection</div>
<svg class="abs" style="left:94px;top:237px" width="24" height="24" viewBox="0 0 24 24"><circle cx="12" cy="12" r="11" fill="#fff" stroke="#bbb" stroke-width="2"/><path d="M14 7l-5 5 5 5" fill="none" stroke="#333" stroke-width="2.5"/></svg>
<svg class="abs" style="left:754px;top:237px" width="24" height="24" viewBox="0 0 24 24"><circle cx="12" cy="12" r="11" fill="#fff" stroke="#bbb" stroke-width="2"/><path d="M10 7l5 5-5 5" fill="none" stroke="#333" stroke-width="2.5"/></svg>
<div class="abs dots"><span class="dot on"></span><span class="dot"></span><span class="dot"></span></div>

<h2 class="abs" style="left:94px;top:416px">Welcome to our website!!</h2>
<p class="abs welcome-text">Thank you for visiting us! You are one step closer to experiencing first class maid service! Our company specializes in detailed housekeeping, janitorial, and commerical cleaning services making your environment shine and sparkle like it never has before! Our maids are fully trained professionals who we recruit from high end luxury hotels we know, like the Grand Meridian and Bayview Suites! We pride ourselves in delivering exceptional service to our valued customers by fully understanding what your expectations &amp; needs are! We will strive for perfection and we will provide an uncompromising</p>
<div class="abs more" style="left:94px;top:550px">Read More +</div>
<div class="abs video" role="img" aria-label="Food pyramid of fruits, vegetables and grains"></div>
<svg class="abs" style="left:645px;top:467px" width="42" height="42" viewBox="0 0 42 42"><circle cx="21" cy="21" r="20" fill="#d9362c"/><path d="M16 12l13 9-13 9z" fill="#fff"/></svg>

<h2 class="abs" style="left:94px;top:599px">Health</h2>
<div class="abs card" style="left:94px;background:linear-gradient(#f3c53b,#e9a91b 60%,#d4d8b0)" role="img" aria-label="Corn cobs with a syringe"></div>
<div class="abs card" style="left:330px;background:radial-gradient(circle at 50% 55%,#9a2a2a,#6b3a28 45%,#3a3a34)" role="img" aria-label="Raw red meat with vegetables"></div>
<div class="abs card" style="left:564px;background:linear-gradient(#6b6b6b,#4a4a4a)" role="img" aria-label="Woman holding food"></div>
<div class="abs food-tips" style="left:564px;top:676px;width:212px;text-align:center">Food Tips</div>
<div class="abs btn" style="left:625px;top:722px;width:91px;height:26px;background:linear-gradient(#7ccb48,var(--green-dark))">CLICK HERE</div>

<div class="abs card-title" style="left:94px;top:794px">GMO</div>
<p class="abs small" style="left:94px;top:815px;width:212px">Lorem ipsum dolor sit amet, consectetuer adipisc-ing elit, sed diam nonummy nibh euismod tincidunt ut laoreet dolore magna aliquam erat volutpat. Lorem ipsum dolor sit amet, consectetuer adipisc-ing elit, sed diam nonummy .</p>
<div class="abs more" style="left:94px;top:903px">Read More +</div>

<div class="abs card-title" style="left:331px;top:794px">Animal Foods</div>
<table class="abs spec" style="left:331px;top:813px;width:212px;border-collapse:collapse">
<tr><td>Type :</td><td>Master Planned Single Family</td></tr>
<tr><td>Size :</td><td>600 units at build-out</td></tr>
<tr><td>Amenities:</td><td style="line-height:16px;padding-top:3px">State-of-the-art community with swim center and shady parks.</td></tr>
</table>
<div class="abs more" style="left:332px;top:903px">Read More +</div>

<div class="abs newsletter">
  <h3>NewsLetters</h3>
  <p>Find a HomeLocal office nearest you by entering your zip code below</p>
  <div class="field">Email</div>
  <div class="btn" style="margin:8px 0 0 152px;width:37px;height:18px;background:var(--green)">Send</div>
</div>

<div class="abs" style="left:95px;top:964px;font-family:'Ubuntu',sans-serif;font-weight:300;color:var(--green);font-size:15px">Testimonials</div>
<div class="abs rule"></div>
<div class="abs" style="left:510px;top:972px;display:flex;gap:3px"><span class="dot" style="width:8px;height:8px;background:var(--orange);border-color:var(--orange)"></span><span class="dot" style="width:8px;height:8px"></span><span class="dot" style="width:8px;height:8px"></span></div>

<div class="abs avatar" style="left:94px;top:1003px" role="img" aria-label="Portrait of a smiling client"></div>
<div class="abs quote-title" style="left:173px;top:1003px">Lorem ipsum dolor sit amet</div>
<p class="abs quote" style="left:172px;top:1018px">Lorem ipsum dolor sit amet, consetetur sadipscing elitr, sed diam nonumy</p>
<div class="abs more" style="left:172px;top:1060px">Read More +</div>

<div class="abs avatar" style="left:328px;top:999px" role="img" aria-label="Portrait of a client"></div>
<div class="abs quote-title" style="left:408px;top:1003px">Lorem ipsum dolor sit amet</div>
<p class="abs quote" style="left:408px;top:1018px">Lorem ipsum dolor sit amet, consetetur sadipscing elitr, sed diam nonumy</p>
<div class="abs more" style="left:409px;top:1060px">Read More +</div>

<h2 class="abs" style="left:564px;top:966px;font-size:19px">Quick Contact</h2>
<p class="abs" style="left:566px;top:997px;width:210px;font-size:8.8px;line-height:14.5px;color:#888">Nunc tempus felis vitae urna Vivamus porttitor g purus nisi eleifend libero a tempus libero lectus</p>
<div class="abs btn" style="left:564px;top:1032px;width:90px;height:26px;background:linear-gradient(var(--orange-light),var(--orange))">CLICK HERE</div>

<div class="abs footer-links">Home<i>|</i>Our Services<i>|</i>About us<i>|</i>Testimonials<i>|</i>Contact Us<i>|</i>Blog</div>
<div class="abs copy">© 2014 Company Name &nbsp;All right reserved &nbsp;Term of Use</div>
<div class="abs social" aria-label="Social links"><span></span><span></span><span></span><span></span></div>
</body>
</html>
```